Business Cards for new orthopaedic surgery practice

My husband and I are starting our own orthopaedic surgery practice. We are looking for a business card that is uniform, but one will have my name/title and the other will have his. You can just create one design with my name on it for now. But when I choose your design as the winning design I will ask that you add another copy with his name/title.

We are looking for classy, simple, elite all in one. We like dark blues/a little gold/yellow. Something that goes with our logo. We want our logo incorporated. Here is all the info you need:
Business name: RV Bone & Vitality Center
Location: 38517 North Willowmere Ave
Palm Hollow, FL 33498
Phone: 954-218-4063
Fax: 954-582-7341
Email: info@myrvbonecare.example

Names: Lydia Vance, M.D.
Board Certified Hand and Upper Extremity Surgeon

Ebo Dansu, M.D.
Board Certified Hip & Knee Replacement/General Orthopaedic Surgeon

Can decide what you want to put on the back. Maybe a slogan:
Grounded in Care. Centered on You

I am just going to upload our logo. The only thing is if we select you as the winning design, the location, and phone numbers may change. We will need your help to update that once fully solidified.

Industry/Entity Type

Medical

Contact Information for Business Card

Colors
0054AA
0677BA
7BADD7
CADEEF
E8F1F8
0094D4
00A9DD
6FCCEA
C7EBF8
E9F6FB

Requirements
Must have
• class, appeal,
Should not have
• We want to air on the side of masculine if we are looking at masculine vs. feminine feel. But we still want it classy, sophisticated, and something we will love

```html
<!DOCTYPE html>
<html lang="en">
<head>
<meta charset="utf-8">
<title>RV Bone &amp; Vitality Center — Business Card</title>
<link rel="stylesheet" href="https://fonts.googleapis.com/css2?family=Cormorant+Garamond:wght@700&family=Montserrat:wght@400;500&display=swap">
<style>
  :root {
    --backdrop: #2b2c2f;
    --card-navy: #1b2a4f;
    --card-navy-deep: #111c3a;
    --card-navy-soft: #3d5283;
    --gold: #c9a55a;
    --ink-white: #ffffff;
  }
  * { margin: 0; padding: 0; box-sizing: border-box; }
  html, body { width: 1200px; height: 1200px; overflow: hidden; }
  body {
    background: var(--backdrop);
    font-family: "Montserrat", sans-serif;
    display: flex;
    align-items: center;
    justify-content: center;
    gap: 60px;
  }
  .card {
    position: relative;
    width: 420px;
    height: 700px;
    background: var(--card-navy);
    border-radius: 28px;
    overflow: hidden;
    box-shadow: 0 18px 40px rgba(0,0,0,0.45);
  }

  /* Front */
  .card-front__details {
    position: absolute;
    top: 70px;
    right: 46px;
    text-align: right;
    color: var(--ink-white);
    z-index: 1;
  }
  .doctor-name {
    font-family: "Cormorant Garamond", serif;
    font-weight: 700;
    font-size: 32px;
    letter-spacing: 0.02em;
    text-transform: uppercase;
    color: var(--gold);
    line-height: 1.1;
  }
  .doctor-title {
    font-size: 17px;
    line-height: 1.25;
    margin-top: 6px;
  }
  .address {
    font-size: 17px;
    line-height: 1.4;
    margin-top: 22px;
  }
  .contact-list {
    list-style: none;
    margin-top: 24px;
    font-size: 17px;
    line-height: 1.55;
  }
  .contact-list li {
    display: flex;
    justify-content: flex-end;
    align-items: center;
    gap: 10px;
  }
  .contact-list svg { width: 16px; height: 16px; fill: var(--gold); }
  .gold-tab {
    position: absolute;
    top: 150px;
    right: 0;
    width: 26px;
    height: 90px;
    background: var(--gold);
  }
  .emblem-watermark {
    position: absolute;
    left: -40px;
    bottom: -40px;
    width: 420px;
    height: 420px;
    background: radial-gradient(circle at 50% 45%, var(--card-navy-soft) 0%, var(--card-navy-deep) 45%, rgba(27,42,79,0) 70%);
    opacity: 0.75;
  }

  /* Back */
  .card-back__brand {
    position: absolute;
    top: 250px;
    left: 0;
    right: 0;
    display: flex;
    flex-direction: column;
    align-items: center;
    gap: 22px;
  }
  .brand-dot {
    width: 46px;
    height: 46px;
    border-radius: 50%;
    border: 2px solid var(--gold);
  }
  .brand-name {
    font-family: "Cormorant Garamond", serif;
    font-weight: 700;
    font-size: 34px;
    letter-spacing: 0.12em;
    text-transform: uppercase;
    text-align: center;
    line-height: 1.2;
    color: var(--ink-white);
  }
  .slogan {
    position: absolute;
    bottom: 70px;
    left: 0;
    right: 0;
    text-align: center;
    font-size: 19px;
    font-weight: 500;
    color: var(--gold);
  }
</style>
</head>
<body>
  <section class="card card-front">
    <div class="emblem-watermark" role="img" aria-label="Faint tone-on-tone practice emblem decoration"></div>
    <div class="gold-tab"></div>
    <div class="card-front__details">
      <h1 class="doctor-name">Lydia Vance, M.D.</h1>
      <p class="doctor-title">Board Certified Hand and Upper<br>Extremity Surgeon</p>
      <p class="address">38517 North Willowmere Ave<br>Palm Hollow, FL 33498</p>
      <ul class="contact-list">
        <li>954-218-4063
          <svg viewBox="0 0 24 24" aria-label="Phone"><path d="M6.6 10.8a15 15 0 0 0 6.6 6.6l2.2-2.2a1 1 0 0 1 1-.25 11.4 11.4 0 0 0 3.6.57 1 1 0 0 1 1 1V20a1 1 0 0 1-1 1A17 17 0 0 1 3 4a1 1 0 0 1 1-1h3.5a1 1 0 0 1 1 1c0 1.250.2 2.45.57 3.57a1 1 0 0 1-.25 1z"/></svg>
        </li>
        <li>954-582-7341
          <svg viewBox="0 0 24 24" aria-label="Fax"><path d="M7 3h10v4H7zM4 8h16a2 2 0 0 1 2 2v6h-4v5H6v-5H2v-6a2 2 0 0 1 2-2zm4 8v3h8v-3z"/></svg>
        </li>
        <li>info@myrvbonecare.example
          <svg viewBox="0 0 24 24" aria-label="Email"><path d="M2 5h20v14H2zm2 2v.5l8 5 8-5V7zm0 2.8V17h16V9.8l-8 5z"/></svg>
        </li>
      </ul>
    </div>
  </section>

  <section class="card card-back">
    <div class="card-back__brand">
      <span class="brand-dot"></span>
      <p class="brand-name">RV Bone &amp;<br>Vitality Center</p>
    </div>
    <p class="slogan">Grounded in Care. Centered on You</p>
  </section>
</body>
</html>
```